Ridgeway Mining Solutions Business Card

Ridgeway Mining Solutions is a company that provides consulting services to the Mining Industry.

Whilst Ridgeway Mining Solutions is an Australian based company its client base is the global mining industry.

The essence of Ridgeway Mining Solutions is its a can do organisation that can make a difference to its clients by providing quality assistance and form lasting relationships.
Updates

Target Market(s)

The global Mining Industry.

Industry/Entity Type

Mining

Font styles to use
Serif

Colors

Designer to choose colors to be used in the design.

Requirements
Nice to have
• My thinking is the card would look good in black given the logo.

I would like to see written on the back side of the card " Providing Metallurgical, Management and Corporate Services to the Mining Industry"

```html
<!DOCTYPE html>
<html lang="en">
<head>
<meta charset="utf-8">
<title>Ridgeway Mining Solutions – Business Card</title>
<link href="https://fonts.googleapis.com/css2?family=Open+Sans:wght@300;400;700&display=swap" rel="stylesheet">
<style>
  :root {
    --backdrop: #d9d9d6;
    --card-black: #07030c;
    --card-white: #ffffff;
    --brand-orange: #e8961c;
    --ink: #1a1a1a;
    --ink-soft: #3a3a3a;
    --band-text: #e6e6e6;
    --tagline: #bdbdbd;
  }
  html, body {
    margin: 0;
    padding: 0;
    width: 1200px;
    height: 902px;
    overflow: hidden;
    background: var(--backdrop);
    font-family: "Open Sans", Arial, sans-serif;
  }
  .canvas {
    width: 1200px;
    height: 902px;
    display: flex;
    align-items: center;
    justify-content: center;
    gap: 60px;
  }
  .card {
    position: relative;
    width: 540px;
    height: 320px;
    box-shadow: 0 6px 18px rgba(0,0,0,0.18);
    overflow: hidden;
  }

  /* Front */
  .card--front {
    background: var(--card-black);
    display: flex;
    flex-direction: column;
    align-items: center;
    justify-content: center;
    gap: 14px;
  }
  .wordmark {
    display: flex;
    align-items: center;
    gap: 10px;
    color: var(--brand-orange);
    font-weight: 700;
    text-transform: uppercase;
    letter-spacing: 0.06em;
    line-height: 1;
    margin: 0;
  }
  .wordmark__square {
    width: 14px;
    height: 14px;
    background: var(--brand-orange);
    flex: none;
  }
  .card--front .wordmark { font-size: 20px; }
  .tagline {
    margin: 0;
    max-width: 380px;
    text-align: center;
    font-size: 11px;
    font-weight: 400;
    line-height: 1.5;
    letter-spacing: 0.04em;
    color: var(--tagline);
  }

  /* Back */
  .card--back { background: var(--card-white); }
  .card--back .wordmark {
    position: absolute;
    top: 26px;
    left: 28px;
    font-size: 11px;
    gap: 6px;
  }
  .card--back .wordmark__square { width: 9px; height: 9px; }
  .contact {
    position: absolute;
    right: 30px;
    top: 108px;
    text-align: right;
    color: var(--ink);
  }
  .contact__name {
    font-size: 26px;
    font-weight: 300;
    margin: 0;
    line-height: 1.1;
  }
  .contact__title {
    font-size: 13px;
    margin: 2px 0 18px;
    color: var(--ink-soft);
  }
  .contact__line {
    font-size: 12px;
    margin: 4px 0;
    color: var(--ink-soft);
  }
  .band {
    position: absolute;
    left: 0;
    right: 0;
    bottom: 0;
    height: 46px;
    background: var(--card-black);
    display: flex;
    align-items: center;
    justify-content: flex-end;
    padding-right: 30px;
    color: var(--band-text);
    font-size: 13px;
    letter-spacing: 0.02em;
  }
</style>
</head>
<body>
<main class="canvas">
  <section class="card card--front" aria-label="Card front">
    <p class="wordmark"><span class="wordmark__square"></span>Ridgeway Mining Solutions</p>
    <p class="tagline">Providing Metallurgical, Management and Corporate Services to the Mining Industry</p>
  </section>

  <section class="card card--back" aria-label="Card back">
    <p class="wordmark"><span class="wordmark__square"></span>Ridgeway Mining Solutions</p>
    <div class="contact">
      <p class="contact__name">Name</p>
      <p class="contact__title">Title</p>
      <p class="contact__line">xxx.xxx.xxxx</p>
      <p class="contact__line">email@email.com</p>
      <p class="contact__line">Address</p>
    </div>
    <div class="band">www.web.com</div>
  </section>
</main>
</body>
</html>
```